Velvet Lantern rebranding my business with a new business card

I have my new logo and now I need a refresher on my business cards. I really want something fun and fresh. I like black background or anything to make the color pop.
Logo
Name: Velvet Lantern
Contact Info as stated below:
Mira Pellow
555-013-4762
Logo
Name: Velvet Lantern
Mira Pellow
555-013-4762
fb.me/VelvetLanternbyMira
Instagram: @VelvetLanternbyMira

Industry/Entity Type

Business

Contact Information for Business Card

double-sided. Logo on one side. Contact info on the other.

Requirements
Must have
• Logo
• Name: Velvet Lantern
• Contact Info as stated below:
• Mira Pellow
• 555-013-4762
• fb.me/VelvetLanternbyMira
• fb.me/VelvetLanternbyMira

```html
<!DOCTYPE html>
<html lang="en">
<head>
<meta charset="utf-8">
<title>Velvet Lantern — Business Card</title>
<link rel="stylesheet" href="https://fonts.googleapis.com/css2?family=Roboto:wght@400;500&family=Roboto+Condensed:wght@700&display=swap">
<style>
  :root {
    --canvas-bg: #ecebe8;
    --card-white: #ffffff;
    --card-black: #1c1c1d;
    --accent-pink: #f2a9bd;
    --ink-dark: #2a2a2a;
    --ink-grey: #5a5a5a;
    --ink-light: #f4f4f4;
    --brand-mauve: #c9668a;
  }
  * { margin: 0; padding: 0; box-sizing: border-box; }
  html, body {
    width: 1200px; height: 960px; overflow: hidden;
    background: var(--canvas-bg);
    font-family: "Roboto", Arial, sans-serif;
  }
  .canvas { position: relative; width: 1200px; height: 960px; }

  .card {
    position: absolute; width: 600px; height: 344px;
    border-radius: 16px; overflow: hidden;
    box-shadow: 0 3px 10px rgba(0,0,0,0.18);
  }

  /* Front side */
  .card-front { left: 320px; top: 96px; background: var(--card-white); }
  .front-badge {
    position: absolute; left: 193px; top: 67px;
    width: 208px; height: 208px; border-radius: 50%;
    border: 3px solid var(--accent-pink);
    display: flex; align-items: center; justify-content: center;
  }
  .brand-name {
    font-family: "Roboto Condensed", "Arial Narrow", sans-serif;
    font-weight: 700; color: var(--brand-mauve);
    text-transform: uppercase; text-align: center; line-height: 1.1;
  }
  .front-badge .brand-name { font-size: 26px; letter-spacing: 1px; }
  .front-url {
    position: absolute; left: 0; right: 0; top: 314px;
    text-align: center; font-size: 15px; letter-spacing: 5.6px;
    color: var(--ink-grey);
  }

  /* Back side */
  .card-back { left: 320px; top: 493px; background: var(--card-black); }
  .back-shapes { position: absolute; inset: 0; }
  .name-tab {
    position: absolute; left: 0; top: 32px; width: 14px; height: 24px;
    background: var(--accent-pink); border-radius: 0 7px 7px 0;
  }
  .holder-name {
    position: absolute; left: 32px; top: 32px;
    font-family: "Roboto Condensed", "Arial Narrow", sans-serif;
    font-weight: 700; font-size: 21px; color: var(--card-white);
    text-transform: uppercase; line-height: 24px;
  }
  .contact-list {
    position: absolute; left: 32px; top: 254px; list-style: none;
  }
  .contact-item {
    display: flex; align-items: center; height: 19.5px;
    font-size: 14px; color: var(--ink-light);
  }
  .contact-icon { width: 13px; height: 13px; margin-right: 9px; fill: var(--ink-light); }
  .back-brand {
    position: absolute; left: 300px; top: 140px; width: 260px;
  }
  .back-brand .brand-name { font-size: 38px; letter-spacing: 1.5px; }
</style>
</head>
<body>
<main class="canvas">

  <section class="card card-front" aria-label="Card front">
    <div class="front-badge">
      <span class="brand-name">Velvet<br>Lantern</span>
    </div>
    <p class="front-url">www.velvetlantern.com</p>
  </section>

  <section class="card card-back" aria-label="Card back">
    <svg class="back-shapes" width="600" height="344" viewBox="0 0 600 344">
      <circle cx="480" cy="172" r="247" fill="none" stroke="var(--accent-pink)" stroke-width="3"/>
      <circle cx="480" cy="172" r="240" fill="none" stroke="var(--accent-pink)" stroke-width="3"/>
      <circle cx="480" cy="172" r="236" fill="var(--card-white)"/>
    </svg>

    <div class="name-tab"></div>
    <h1 class="holder-name">Mira Pellow</h1>

    <ul class="contact-list">
      <li class="contact-item">
        <svg class="contact-icon" viewBox="0 0 24 24"><path d="M6.6 10.8a15.1 15.1 0 0 0 6.6 6.6l2.2-2.2a1 1 0 0 1 1-.25 11.4 11.4 0 0 0 3.6.57 1 1 0 0 1 1 1V20a1 1 0 0 1-1 1A17 17 0 0 1 3 4a1 1 0 0 1 1-1h3.5a1 1 0 0 1 1 1c0 1.25.2 2.45.57 3.57a1 1 0 0 1-.25 1z"/></svg>
        555-013-4762
      </li>
      <li class="contact-item">
        <svg class="contact-icon" viewBox="0 0 24 24"><circle cx="12" cy="12" r="10" fill="none" stroke="var(--ink-light)" stroke-width="2.4"/><path d="M2 12h20M12 2c3 3 3 17 0 20M12 2c-3 3-3 17 0 20" fill="none" stroke="var(--ink-light)" stroke-width="2"/></svg>
        www.velvetlantern.com
      </li>
      <li class="contact-item">
        <svg class="contact-icon" viewBox="0 0 24 24"><rect x="2" y="2" width="20" height="20" rx="2"/></svg>
        fb.me/VelvetLanternbyMira
      </li>
    </ul>

    <div class="back-brand">
      <p class="brand-name">Velvet<br>Lantern</p>
    </div>
  </section>

</main>
</body>
</html>
```